Need help in designing new business card utilizing our new logo.

BuildMark Solutions works with Construction Business Owners, Managers & IT Professionals to strengthen software usage and increase user productivity.

Our Construction Accounting and Mobile Field Management Software Clients engage with us in the following areas:

New Software Implementations
Software Re-Implementations
Redesigning Software Usage at the User Level
Project Coordination & Management
Continued Software Support

Old tag line:
Weighing Options - Implementing Solutions

www.buildmark-solutions.example

Ridge 4 is a product, but not needed for a new business card.

```html
<!DOCTYPE html>
<html lang="en">
<head>
<meta charset="utf-8">
<title>BuildMark Solutions – Business Card</title>
<link rel="stylesheet" href="https://fonts.googleapis.com/css2?family=Arimo:wght@400;700&display=swap">
<style>
  :root {
    --brand-blue: #2323a8;
    --text-grey: #6f6f6f;
    --card-white: #ffffff;
    --backdrop: #e9e8ec;
    --shadow: rgba(30, 30, 60, 0.18);
  }
  * { box-sizing: border-box; margin: 0; padding: 0; }
  html, body {
    width: 1200px; height: 675px; overflow: hidden;
    background: var(--backdrop);
    font-family: "Arimo", Arial, sans-serif;
  }
  .stage {
    width: 1200px; height: 675px;
    display: flex; align-items: center; justify-content: center; gap: 60px;
  }
  .card {
    position: relative;
    width: 500px; height: 286px;
    box-shadow: 0 10px 28px var(--shadow);
  }
  .card--front { background: var(--card-white); }
  .card--back { background: var(--brand-blue); }

  .brand {
    position: absolute;
    display: flex; align-items: center; gap: 12px;
    font-weight: 700; white-space: nowrap;
  }
  .brand__square { width: 26px; height: 26px; }
  .card--front .brand {
    top: 48px; left: 50%; transform: translateX(-50%);
    color: var(--brand-blue); font-size: 30px;
  }
  .card--front .brand__square { background: var(--brand-blue); }
  .card--back .brand {
    top: 50%; left: 50%; transform: translate(-50%, -50%);
    color: var(--card-white); font-size: 36px;
  }
  .card--back .brand__square { width: 32px; height: 32px; background: var(--card-white); }

  .divider {
    position: absolute; left: 150px; right: 34px; top: 168px;
    height: 2px; background: var(--brand-blue);
  }
  .person { position: absolute; left: 30px; top: 146px; }
  .person__name {
    color: var(--brand-blue); font-weight: 700; font-size: 19px;
    letter-spacing: 0.3px; text-transform: uppercase;
  }
  .person__role { color: var(--text-grey); font-size: 13px; margin-top: 12px; }

  .address {
    position: absolute; right: 34px; top: 186px;
    text-align: right; color: var(--text-grey); font-size: 13px; line-height: 1.5;
  }
  .contacts {
    position: absolute; left: 30px; bottom: 24px;
    list-style: none; color: var(--text-grey); font-size: 13px;
  }
  .contacts li { display: flex; align-items: center; gap: 9px; margin-top: 7px; }
  .contacts svg { width: 18px; height: 18px; flex: none; }

  .website {
    position: absolute; right: 30px; bottom: 24px;
    color: var(--card-white); font-size: 14px; letter-spacing: 0.4px;
  }
</style>
</head>
<body>
<main class="stage">
  <section class="card card--front" aria-label="Business card front">
    <div class="brand"><span class="brand__square"></span>BuildMark Solutions</div>
    <div class="divider"></div>
    <div class="person">
      <p class="person__name">Dana R. Whitlock</p>
      <p class="person__role">Owner</p>
    </div>
    <address class="address">
      14B Meridian Street - PMB 108<br>
      Lakeview Falls NY 10472
    </address>
    <ul class="contacts">
      <li>
        <svg viewBox="0 0 18 18" aria-hidden="true">
          <circle cx="9" cy="9" r="9" fill="var(--brand-blue)"/>
          <path d="M6.2 4.6l1.6 1.9-.9 1.2c.6 1.3 1.5 2.2 2.8 2.8l1.2-.9 1.9 1.6-.9 1.5c-3.4-.3-6.4-3.3-6.7-6.7z" fill="#fff"/>
        </svg>
        555-014-2387
      </li>
      <li>
        <svg viewBox="0 0 18 18" aria-hidden="true">
          <circle cx="9" cy="9" r="9" fill="var(--brand-blue)"/>
          <rect x="4.5" y="5.8" width="9" height="6.4" fill="none" stroke="#fff" stroke-width="1.2"/>
          <path d="M4.5 5.8L9 9.6l4.5-3.8" fill="none" stroke="#fff" stroke-width="1.2"/>
        </svg>
        dwhitlock@buildmark-solutions.example
      </li>
    </ul>
  </section>

  <section class="card card--back" aria-label="Business card back">
    <div class="brand"><span class="brand__square"></span>BuildMark Solutions</div>
    <p class="website">www.buildmark-solutions.example</p>
  </section>
</main>
</body>
</html>
```